Korvath Supply Website Redesign

Currently korvathsupply.example is focussed on fulfillment and transport from various products in the BBQ segment. However, no we want to update our business activities to Product Development, Brand Development, Online Positioning, Logistics & Aftersales, and Promotional BBQs. We will be a business for Outdoor Leisure Development from A to Z.

Therefore, we need a brand new website. The colours of the current website may be the same. However, i'd like to keep it clean. More white and use blue and green as accent colours. It is a business to business organization so the website should be looking formal and corporate. However we sell fun products so not too formal and corporate.

Pages we need; Home, About, Contact, Our Services (+ page per service) a place to share our news/blogs.

I have added some sort of mock up of an idea. However it needs some finetuning.

Target Market(s)

Businesses

Industry/Entity Type

Corporate/Logistics/Marketing

Coding

Coded - Design and coding required

Colors

Designer to choose colors to be used in the design.

Requirements
Must have
• Show clear distinguishing of the different services we provide (Product Development, Brand Development, Online Positioning, Logistics & Aftersales and Promotional BBQs). Every service should have its own page too. Besides, I would like to have a blog page to share relevant content.
Nice to have
• Show that we are the expert in Outdoor LEisure Development from A to Z
Should not have
• Be too informal. It may be semi-formal

```html
<!DOCTYPE html>
<html lang="en">
<head>
<meta charset="utf-8">
<title>Korvath Supply — Home</title>
<link href="https://fonts.googleapis.com/css2?family=Work+Sans:wght@400;500;600;700&display=swap" rel="stylesheet">
<style>
:root{
  --navy:#0e1c3a;
  --navy-soft:#16264a;
  --green:#34a03c;
  --green-soft:#4bb152;
  --ink:#1b2233;
  --muted:#5d6472;
  --white:#ffffff;
  --footer-text:#dfe4ee;
}
*{box-sizing:border-box;margin:0;padding:0}
html,body{width:1200px;height:4695px;overflow:hidden}
body{font-family:"Work Sans",Arial,sans-serif;color:var(--ink);background:var(--white)}
.page{position:relative;width:1200px;height:4695px;overflow:hidden}
.abs{position:absolute}
.bg-shapes{position:absolute;left:0;top:0;width:1200px;height:4695px}
a{color:inherit;text-decoration:none}
ul{list-style:none}

/* header */
.brand{display:flex;align-items:center;gap:8px;font-weight:700;font-size:34px;color:var(--white);letter-spacing:.5px}
.brand-dot{width:20px;height:20px;border-radius:50%;background:var(--green)}
.nav{left:315px;top:30px;display:flex;font-size:14px;color:var(--white)}
.nav a{margin-right:27px}
.nav .active{color:var(--green-soft)}
.search-btn{left:784px;top:24px;width:30px;height:30px;border-radius:50%;background:#25345a;display:flex;align-items:center;justify-content:center}
.lang{left:848px;top:30px;font-size:14px;color:var(--white)}
.login{left:1001px;top:22px;width:88px;height:35px;border-radius:4px;background:var(--green);color:var(--white);font-size:14px;font-weight:600;display:flex;align-items:center;justify-content:center;gap:6px}

/* hero */
.hero-title{left:110px;top:222px;font-size:36px;font-weight:600;color:var(--white)}
.hero-text{left:112px;top:284px;width:430px;font-size:15px;line-height:26px;color:#dfe4ee}
.btn{display:inline-flex;align-items:center;justify-content:center;background:var(--green);color:var(--white);font-weight:500;border-radius:4px}
.hero-btn{left:111px;top:386px;width:146px;height:50px;font-size:18px}
.hero-photo{left:711px;top:118px;width:489px;height:489px;border-radius:50%;background:radial-gradient(circle at 45% 40%,#c9b3a0 0%,#8e7a6e 35%,#4a4e5c 70%,#2c3446 100%)}

.feature-card{top:569px;width:288px;height:219px;border-radius:6px;background:var(--white);box-shadow:0 6px 18px rgba(14,28,58,.14);text-align:center;padding:24px 22px 0}
.feature-card.is-active{background:var(--green);color:var(--white)}
.feature-card svg{display:block;margin:0 auto 12px}
.feature-card h3{font-size:15px;font-weight:600;margin-bottom:7px}
.feature-card p{font-size:11.5px;line-height:21px;color:var(--muted)}
.feature-card.is-active p{color:#eaf6ea}

.divider{left:110px;top:869px;width:980px;height:2px;background:var(--green)}
.eyebrow{font-size:14.5px;font-weight:600;letter-spacing:.3px;color:var(--ink);text-transform:uppercase}
.special-eyebrow{left:111px;top:943px}
.special-title{left:110px;top:975px;font-size:41px;line-height:46px;font-weight:600;color:var(--green)}
.special-text{left:514px;top:958px;width:578px;font-size:14.5px;line-height:31px;color:var(--muted)}

/* services */
.center-head{left:0;width:1200px;text-align:center}
.on-green .eyebrow{color:var(--navy)}
.section-title{font-size:40px;font-weight:600}
.title-white{color:var(--white)}
.title-navy{color:var(--navy)}
.service-card{top:1362px;width:296px;height:345px;background:var(--white);border-radius:4px;overflow:hidden;text-align:center}
.service-card .ph{height:232px}
.service-card h3{font-size:20px;font-weight:600;margin-top:15px}
.service-card .more{display:inline-block;margin-top:18px;font-size:19px;font-weight:600;color:#4a5060;text-decoration:underline;text-underline-offset:4px}
.service-card.is-hover .ph{position:absolute;inset:0;height:auto}
.service-card.is-hover .overlay{position:absolute;inset:0;background:linear-gradient(180deg,rgba(14,28,58,.15) 30%,rgba(14,28,58,.92) 80%)}
.service-card.is-hover .caption{position:absolute;left:0;right:0;bottom:22px;color:var(--white);padding:0 30px}
.service-card.is-hover h3{margin:0 0 12px}
.service-card.is-hover p{font-size:12px;line-height:20px}
.arrow-btn{width:30px;height:30px;border-radius:50%;background:var(--white);display:flex;align-items:center;justify-content:center}
.btn-navy{background:var(--navy);color:var(--white);font-size:19px;font-weight:500;border-radius:4px;display:flex;align-items:center;justify-content:center}

/* method */
.method-photo{left:114px;top:2003px;width:400px;height:400px;border-radius:50%;background:linear-gradient(160deg,#7b5a3c 0%,#c79a5a 30%,#9aa6b8 60%,#d99a2d 85%,#5d6c86 100%)}
.method-eyebrow{left:566px;top:2048px}
.method-title{left:558px;top:2090px;font-size:41px;font-weight:600;color:var(--navy)}
.method-text{left:568px;top:2156px;width:510px;font-size:14.5px;line-height:31px;color:var(--muted)}
.method-btn{left:569px;top:2345px;width:146px;height:50px;font-size:19px}

/* blog */
.blog-card{top:2723px;height:325px;background:var(--white);border-radius:4px;overflow:hidden}
.blog-card .body{padding:12px 20px 0}
.blog-card .meta{font-size:11px;color:var(--muted)}
.blog-card h3{font-size:14.5px;font-weight:600;margin:6px 0}
.blog-card p{font-size:11.5px;line-height:20px;color:var(--muted)}
.blog-card p b{color:var(--ink);font-weight:600}
.blog-card.wide{display:flex}

/* partners */
.partner{width:288px;height:140px;display:flex;align-items:center;justify-content:center;gap:8px;font-size:30px;font-weight:700;color:#3a3f4a}
.partner.is-hover{background:var(--white);box-shadow:0 6px 22px rgba(14,28,58,.14)}
.partner .mark{width:18px;height:18px;border-radius:50%;background:#5b606b}

/* contact */
.contact-eyebrow{color:var(--green)}
.field{top:4078px;width:298px;height:70px;background:var(--white);border:2px solid #c8ccd4;padding:0 30px;display:flex;align-items:center;font-size:14px;font-weight:600;color:#4a5060}
.submit{left:516px;top:4193px;width:166px;height:53px;font-size:18px;font-weight:700;letter-spacing:.5px}

/* footer */
.foot-line{left:110px;width:980px;height:1px;background:#3b4866}
.foot-brand{left:111px;top:4366px}
.foot-brand .brand{font-size:48px}
.foot-brand .brand-dot{width:28px;height:28px}
.foot-about{left:111px;top:4435px;width:270px;font-size:11px;line-height:22px;color:#c9cfdb}
.follow{left:111px;top:4512px;display:flex;align-items:center;gap:10px;font-size:17px;font-weight:500;color:var(--white)}
.social{width:20px;height:20px;border-radius:50%;background:#1c74c4}
.social.sq{border-radius:4px;background:#e0506a}
.foot-col h4{font-size:17px;font-weight:500;color:var(--white);margin-bottom:14px;letter-spacing:.3px}
.link-list li{font-size:14px;color:var(--footer-text);height:35px}
.link-list li::before{content:"»";margin-right:12px;color:var(--white)}
.contact-list li{display:flex;align-items:flex-start;gap:14px;font-size:14px;color:var(--footer-text);line-height:17px;margin-bottom:20px}
.contact-list svg{flex:none;margin-top:1px}
.copyright{left:0;top:4648px;width:1200px;text-align:center;font-size:14px;color:var(--footer-text)}
</style>
</head>
<body>
<div class="page">

  <svg class="bg-shapes" viewBox="0 0 1200 4695" aria-hidden="true">
    <path d="M0 0H1200V560Q760 520 300 560Q120 575 0 610Z" fill="#0e1c3a"/>
    <path d="M0 0H290L0 430Z" fill="#16264a" opacity=".6"/>
    <path d="M0 1195Q600 1100 1200 1150V1830Q600 1945 0 1840Z" fill="#34a03c"/>
    <path d="M0 2540Q600 2430 1200 2500V3150Q600 3240 0 3170Z" fill="#34a03c"/>
    <path d="M0 3930Q560 3830 1200 3905V4695H0Z" fill="#0e1c3a"/>
  </svg>

  <header>
    <div class="abs" style="left:111px;top:18px"><div class="brand"><span class="brand-dot"></span>Korvath</div></div>
    <nav class="abs nav">
      <a class="active" href="#">Home</a><a href="#">About</a><a href="#">Our Services</a><a href="#">latest News</a><a href="#">Contact</a>
    </nav>
    <div class="abs search-btn"><svg width="12" height="12" viewBox="0 0 12 12"><circle cx="5" cy="5" r="3.6" fill="none" stroke="#fff" stroke-width="1.5"/><path d="M7.7 7.7L11 11" stroke="#fff" stroke-width="1.5"/></svg></div>
    <div class="abs lang">Language: Dutch</div>
    <a class="abs login" href="#"><svg width="11" height="12" viewBox="0 0 11 12"><rect x="1" y="5" width="9" height="7" rx="1" fill="#fff"/><path d="M3 5V3.5a2.5 2.5 0 0 1 5 0V5" fill="none" stroke="#fff" stroke-width="1.4"/></svg>Login</a>
  </header>

  <section>
    <h1 class="abs hero-title">Welcome To Loyalty Programs</h1>
    <p class="abs hero-text">Managing and executing loyalty programs that include coupon redemption, transaction processing and automated shipping.</p>
    <a class="abs btn hero-btn" href="#">Get Started</a>
    <div class="abs hero-photo" role="img" aria-label="Photo of a smiling woman working on a laptop in an office"></div>
  </section>

  <section>
    <div class="abs feature-card is-active" style="left:133px">
      <svg width="56" height="50" viewBox="0 0 56 50" fill="none" stroke="#fff" stroke-width="2"><rect x="4" y="16" width="40" height="28" rx="3"/><path d="M4 24H44"/><rect x="10" y="32" width="10" height="6"/><circle cx="44" cy="12" r="8" fill="#5cbb62"/><path d="M40 12l3 3 5-6"/></svg>
      <h3>Loyalty Programs</h3>
      <p>Managing and executing loyalty programs that include coupon redemption, transaction processing and automated shipping...Read More</p>
    </div>
    <div class="abs feature-card" style="left:456px">
      <svg width="66" height="50" viewBox="0 0 66 50" fill="none" stroke="#1b2233" stroke-width="2"><rect x="4" y="20" width="26" height="16"/><path d="M30 26h10l6 8v2H30"/><circle cx="12" cy="40" r="4"/><circle cx="38" cy="40" r="4"/><path d="M44 20V6h6v8h6V4h6v26"/></svg>
      <h3>Project Distribution</h3>
      <p>You have devised an original campaign, found the right product and the end result has been fantastic Now you just need to make sure it's on...Read More</p>
    </div>
    <div class="abs feature-card" style="left:779px">
      <svg width="50" height="50" viewBox="0 0 50 50" fill="none" stroke="#1b2233" stroke-width="2.2"><path d="M6 12H44M6 25H44M6 38H44"/><circle cx="30" cy="12" r="4" fill="#fff"/><circle cx="18" cy="25" r="4" fill="#fff"/><circle cx="34" cy="38" r="4" fill="#fff"/></svg>
      <h3>Fullfilment</h3>
      <p>We can process orders automatically via our portals. Depending on the type of collaboration and product, we do this from our own ...Read More</p>
    </div>
  </section>

  <section>
    <div class="abs divider"></div>
    <p class="abs eyebrow special-eyebrow">Korvath Supply</p>
    <h2 class="abs special-title">What makes us<br>Special</h2>
    <p class="abs special-text">We believe that the partners we work for should be able to focus on building their brand and product. Korvath Supply therefore takes care of the process from order processing to delivery....READ MORE</p>
  </section>

  <section class="on-green">
    <div class="abs center-head" style="top:1215px"><p class="eyebrow">Korvath Supply</p></div>
    <div class="abs center-head" style="top:1267px"><h2 class="section-title title-white">Our Services</h2></div>
    <div class="abs arrow-btn" style="left:38px;top:1541px"><svg width="10" height="10" viewBox="0 0 10 10"><path d="M7 1L3 5l4 4" fill="none" stroke="#34a03c" stroke-width="2"/></svg></div>
    <div class="abs arrow-btn" style="left:1125px;top:1541px"><svg width="10" height="10" viewBox="0 0 10 10"><path d="M3 1l4 4-4 4" fill="none" stroke="#34a03c" stroke-width="2"/></svg></div>

    <article class="abs service-card" style="left:111px">
      <div class="ph" role="img" aria-label="Photo of a product team reviewing plans around a table" style="background:linear-gradient(135deg,#c7d3e3,#7d92b3 50%,#3f5f94)"></div>
      <h3>Product Development</h3>
      <a class="more" href="#">Read More</a>
    </article>
    <article class="abs service-card" style="left:452px">
      <div class="ph" role="img" aria-label="Photo of a student sitting with a laptop and backpack" style="background:linear-gradient(135deg,#e8e2d6,#d9b14a 50%,#a7c940)"></div>
      <h3>Online Positioning</h3>
      <a class="more" href="#">Read More</a>
    </article>
    <article class="abs service-card is-hover" style="left:793px">
      <div class="ph" role="img" aria-label="Photo of warehouse workers in hard hats with a tablet" style="background:linear-gradient(160deg,#3e69a8,#5b7fb5 40%,#c6743a 70%,#2a3552)"></div>
      <div class="overlay"></div>
      <div class="caption">
        <h3>Logistics &amp; Aftersales</h3>
        <p>Lorem ipsum dolor sit amet, consectetur adipiscing elit, sed do et dolore magna aliqua...Read More</p>
      </div>
    </article>
    <a class="abs btn-navy" href="#" style="left:528px;top:1766px;width:144px;height:53px">View All</a>
  </section>

  <section>
    <div class="abs method-photo" role="img" aria-label="Photo of a forklift in a tall warehouse aisle"></div>
    <p class="abs eyebrow method-eyebrow">Korvath Supply</p>
    <h2 class="abs method-title">Our Method</h2>
    <p class="abs method-text">Korvath Supply works for various brands with a focus on FMCG, Specialty Products &amp; (high-end) Promotional Merchandise.We believe that the partners we work for should be able to focus on building their brand and product. Korvath Supply therefore takes care of the process from order processing to delivery.</p>
    <a class="abs btn method-btn" href="#">Read More</a>
  </section>

  <section class="on-green">
    <div class="abs center-head" style="top:2563px"><p class="eyebrow">Korvath Supply</p></div>
    <div class="abs center-head" style="top:2617px"><h2 class="section-title title-white">Latest Blog</h2></div>
    <div class="abs arrow-btn" style="left:42px;top:2871px"><svg width="10" height="10" viewBox="0 0 10 10"><path d="M7 1L3 5l4 4" fill="none" stroke="#34a03c" stroke-width="2"/></svg></div>
    <div class="abs arrow-btn" style="left:1130px;top:2871px"><svg width="10" height="10" viewBox="0 0 10 10"><path d="M3 1l4 4-4 4" fill="none" stroke="#34a03c" stroke-width="2"/></svg></div>

    <article class="abs blog-card" style="left:113px;width:224px">
      <div role="img" aria-label="Photo of two colleagues looking at charts on a laptop" style="height:162px;background:linear-gradient(135deg,#b9b3ad,#6f7d90 55%,#c98f6a)"></div>
      <div class="body">
        <p class="meta">Posted By: June 11, 2021</p>
        <h3>Neque porro quisquam</h3>
        <p>Excepteur sint occaecat cupitat non proident, sunt in culpa qui officia deserunt mollit anim id est laborum... <b>Read More</b></p>
      </div>
    </article>
    <article class="abs blog-card" style="left:363px;width:224px">
      <div role="img" aria-label="Photo of two men talking in a warehouse" style="height:162px;background:linear-gradient(135deg,#8aa0bf,#435d88 50%,#c9ced8)"></div>
      <div class="body">
        <p class="meta">Posted By: Oct 23, 2021</p>
        <h3>Consectetur adipisci</h3>
        <p>Excepteur sint occaecat cupitat non proident, sunt in culpa qui officia deserunt mollit anim id est laborum... <b>Read More</b></p>
      </div>
    </article>
    <article class="abs blog-card wide" style="left:611px;width:478px">
      <div role="img" aria-label="Photo of a parent and child working on papers at a table" style="width:224px;height:325px;flex:none;background:linear-gradient(160deg,#d6cfc5,#9b8b7d 50%,#e8e3dc)"></div>
      <div class="body" style="width:254px;padding-top:24px">
        <p class="meta">Posted By: Nov 18, 2021</p>
        <h3>Finibus Bonorum Malorum</h3>
        <p style="line-height:24px">Temporibus autem quibusda ipsum aut officiis debitis aut rerum necbus saepe eveniet ut et voluptates repae sint et molestiae non recusandae. It earum rerum hicttur a sapite deleus, utaut rends voluptats maiores alias couur aut perfendis doloribus asres repellat. Nam libero tempore, cum soluta nobis est eligendi optio cume possimus, omnis dolor repellendus.</p>
      </div>
    </article>
    <a class="abs btn-navy" href="#" style="left:516px;top:3106px;width:144px;height:53px">View All</a>
  </section>

  <section>
    <div class="abs center-head" style="top:3314px"><p class="eyebrow">Korvath Supply</p></div>
    <div class="abs center-head" style="top:3365px"><h2 class="section-title title-navy">Our Partners</h2></div>
    <div class="abs partner" style="left:133px;top:3489px"><span class="mark"></span>Korvath</div>
    <div class="abs partner is-hover" style="left:456px;top:3489px">Sauce Atelier</div>
    <div class="abs partner" style="left:779px;top:3489px">Emberline</div>
    <div class="abs partner" style="left:133px;top:3670px">Kettle &amp; Co</div>
    <div class="abs partner" style="left:456px;top:3670px">Oakhollow</div>
    <div class="abs partner" style="left:779px;top:3670px">Hearthmark</div>
  </section>

  <section>
    <div class="abs center-head" style="top:3940px"><p class="eyebrow contact-eyebrow">Korvath Supply</p></div>
    <div class="abs center-head" style="top:3980px"><h2 class="section-title title-white">Contact Us</h2></div>
    <div class="abs field" style="left:129px">Name</div>
    <div class="abs field" style="left:450px">Phone</div>
    <div class="abs field" style="left:771px">Message</div>
    <a class="abs btn submit" href="#">SUBMIT</a>
  </section>

  <footer>
    <div class="abs foot-line" style="top:4312px"></div>
    <div class="abs foot-brand"><div class="brand"><span class="brand-dot"></span>Korvath</div></div>
    <p class="abs foot-about">Korvath Supply unburdens its customers through the silent distribution of their brand and associated products.</p>
    <div class="abs follow">Follow Us On:<span class="social" role="img" aria-label="Professional network profile"></span><span class="social sq" role="img" aria-label="Photo sharing profile"></span></div>

    <div class="abs foot-col" style="left:440px;top:4362px">
      <h4>QUICK LINKS</h4>
      <ul class="link-list"><li>Home</li><li>About us</li><li>Services</li><li>Latest Blog</li><li>Contact us</li></ul>
    </div>
    <div class="abs foot-col" style="left:635px;top:4362px">
      <h4>SERVICES</h4>
      <ul class="link-list"><li>Logistics</li><li>Aftersales</li><li>Online Positioning</li><li>Product Development</li><li>Brand Development</li></ul>
    </div>
    <div class="abs foot-col" style="left:855px;top:4362px">
      <h4>CONTACT US</h4>
      <ul class="contact-list">
        <li><svg width="12" height="16" viewBox="0 0 12 16"><path d="M6 0a6 6 0 0 1 6 6c0 4-6 10-6 10S0 10 0 6a6 6 0 0 1 6-6z" fill="#fff"/><circle cx="6" cy="6" r="2.2" fill="#0e1c3a"/></svg><span>Linden Quay 12<br>4811 XK Harbourton</span></li>
        <li><svg width="14" height="11" viewBox="0 0 14 11"><rect width="14" height="11" rx="1" fill="#fff"/><path d="M1 1l6 5 6-5" fill="none" stroke="#0e1c3a" stroke-width="1.3"/></svg><span>info@korvathsupply.example</span></li>
        <li><svg width="14" height="14" viewBox="0 0 14 14"><path d="M3 0l3 3-2 2c1 2 3 4 5 5l2-2 3 3-2 3C6 14 0 8 0 3z" fill="#fff"/></svg><span>+31 (0)10 555 0147</span></li>
      </ul>
    </div>

    <div class="abs foot-line" style="top:4620px"></div>
    <p class="abs copyright">2021 Copyright © Korvath Supply</p>
  </footer>

</div>
</body>
</html>
```